Need Business Card for our Real Estate Business with Sales Executive's Picture

PANTONE 484 C ( RED)

PANTONE 2766 C ( BLUE

Industry/Entity Type

Real Estate

Contact Information for Business Card

Name, Mobile, email, & picture of Person
Agency Phone, address, Web address

Requirements
Must have
• Our Logo Colours, Agent Picture,

```html
<!DOCTYPE html>
<html lang="en">
<head>
<meta charset="utf-8">
<title>Meridian Homes – Business Card</title>
<link rel="stylesheet" href="https://fonts.googleapis.com/css2?family=Lato:wght@400;700&display=swap">
<style>
  :root {
    --navy: #272b45;
    --red: #7a2026;
    --white: #ffffff;
    --ink: #1c1c24;
    --backdrop: #e6e7eb;
    --photo-top: #c9ccd6;
    --photo-bottom: #3a4f8f;
  }
  * { margin: 0; padding: 0; box-sizing: border-box; }
  html, body { width: 1200px; height: 900px; overflow: hidden; }
  body { background: var(--backdrop); font-family: "Lato", sans-serif; position: relative; }

  .card { position: absolute; width: 700px; height: 400px; overflow: hidden; box-shadow: 0 6px 18px rgba(0,0,0,.18); }

  /* Back side */
  .card-back { left: 60px; top: 50px; background: var(--navy); color: var(--white); }
  .card-back .brand { position: absolute; left: 0; right: 0; top: 150px; display: flex; justify-content: center; align-items: center; gap: 14px; }
  .card-back .brand-mark { width: 16px; height: 16px; background: var(--red); }
  .card-back .brand-name { font-size: 46px; font-weight: 400; letter-spacing: 6px; }
  .card-back .web { position: absolute; left: 0; right: 0; top: 300px; text-align: center; font-size: 17px; letter-spacing: .5px; }

  /* Front side */
  .card-front { left: 440px; top: 450px; background: var(--white); color: var(--ink); }
  .card-front .decor { position: absolute; inset: 0; }
  .card-front .brand { position: absolute; left: 250px; top: 82px; display: flex; align-items: center; gap: 10px; color: var(--navy); }
  .card-front .brand-mark { width: 12px; height: 12px; background: var(--red); }
  .card-front .brand-name { font-size: 28px; letter-spacing: 3px; }
  .agent { position: absolute; right: 40px; top: 34px; text-align: right; }
  .agent-name { color: var(--red); font-size: 24px; font-weight: 700; }
  .agent-role { font-size: 15px; margin-top: 2px; }
  .contacts { position: absolute; right: 40px; top: 135px; list-style: none; text-align: right; font-size: 15px; line-height: 22px; }
  .contacts li { display: flex; justify-content: flex-end; align-items: center; gap: 8px; }
  .contacts svg { width: 12px; height: 12px; fill: var(--red); flex: none; }
  .address { position: absolute; right: 40px; top: 240px; font-size: 15px; }
</style>
</head>
<body>

<section class="card card-back">
  <div class="brand"><span class="brand-mark"></span><span class="brand-name">MERIDIAN HOMES</span></div>
  <p class="web">www.meridianhomes.com</p>
</section>

<section class="card card-front">
  <svg class="decor" viewBox="0 0 700 400" width="700" height="400">
    <defs>
      <linearGradient id="photoTone" x1="0" y1="0" x2="0" y2="1">
        <stop offset="0" stop-color="var(--photo-top)"/>
        <stop offset="1" stop-color="var(--photo-bottom)"/>
      </linearGradient>
    </defs>
    <rect class="agent-photo" x="70" y="125" width="250" height="260" fill="url(#photoTone)" role="img" aria-label="Portrait photo of the sales executive in a blue suit"/>
    <path d="M665 0 L700 0 L700 60 Z" fill="var(--navy)"/>
    <path d="M0 400 L0 388 C 260 402, 520 372, 700 304 L700 400 Z" fill="var(--navy)"/>
    <path d="M270 390 C 460 376, 600 346, 700 292" stroke="var(--red)" stroke-width="6" fill="none"/>
  </svg>

  <div class="brand"><span class="brand-mark"></span><span class="brand-name">MERIDIAN HOMES</span></div>

  <div class="agent">
    <p class="agent-name">Daniel Hartley</p>
    <p class="agent-role">Manager</p>
  </div>

  <ul class="contacts">
    <li>555 014 2800 <svg viewBox="0 0 24 24"><path d="M6.6 10.8a15 15 0 0 0 6.6 6.6l2.2-2.2a1 1 0 0 1 1-.25 11.4 11.4 0 0 0 3.6.6 1 1 0 0 1 1 1V20a1 1 0 0 1-1 1A17 17 0 0 1 3 4a1 1 0 0 1 1-1h3.5a1 1 0 0 1 1 1c0 1.25.2 2.45.6 3.6a1 1 0 0 1-.25 1z"/></svg></li>
    <li>555 014 2801 <svg viewBox="0 0 24 24"><path d="M7 1h10a2 2 0 0 1 2 2v18a2 2 0 0 1-2 2H7a2 2 0 0 1-2-2V3a2 2 0 0 1 2-2zm0 3v14h10V4z"/></svg></li>
    <li>hello@meridianhomes.com <svg viewBox="0 0 24 24"><path d="M2 4h20v16H2zm2 2v.5l8 5 8-5V6z"/></svg></li>
    <li>www.meridianhomes.com <svg viewBox="0 0 24 24"><circle cx="12" cy="12" r="10"/></svg></li>
  </ul>

  <p class="address">48 Alder Court, Springvale, TX 77000</p>
</section>

</body>
</html>
```